Gemstones e-commerce web-site needs a new template/style

We would like to highlight some of our more exclusive product (gemstones) in a new signature template that has its own style, fonts and colors. The new template would allow for larger and more detailed images. e.g. Tovelcrest.com. The design should account for different sized mobile devices. Current site is http://www.kelvorastones.com

Industry/Entity Type

Product

Number of Pages Required

2 page

```html
<!DOCTYPE html>
<html lang="en">
<head>
<meta charset="utf-8">
<title>Kelvora Stones USA — Jewellery Online Boutique</title>
<link rel="stylesheet" href="https://fonts.googleapis.com/css2?family=Cinzel:wght@400;700&family=Open+Sans:wght@400;600&family=Great+Vibes&display=swap">
<style>
:root{
  --bg:#0b0b0b;
  --panel:#1a1a1a;
  --green:#2f9a4c;
  --green-bright:#3fb35c;
  --white:#ffffff;
  --text:#bdbdbd;
  --muted:#8a8a8a;
  --line:#6c6c6c;
  --nav:#050505;
}
*{box-sizing:border-box;margin:0;padding:0}
html,body{width:1200px;height:3015px;overflow:hidden;background:var(--bg);color:var(--text);font-family:"Open Sans",Arial,sans-serif}
.page{position:relative;width:1200px;height:3015px;overflow:hidden}
.abs{position:absolute}

/* header */
.site-header{position:absolute;left:0;top:0;width:1200px;height:150px;background:linear-gradient(#161616,#0a0a0a)}
.brand{left:100px;top:24px;display:flex;align-items:center;gap:10px}
.brand-mark{width:22px;height:22px;background:var(--green)}
.brand-name{font-weight:600;font-size:24px;color:var(--white)}
.brand-tag{left:132px;top:58px;font-size:13px;color:var(--muted)}
.shipping{left:422px;top:30px;width:214px;height:52px;border:1px solid var(--line);display:flex;align-items:center;justify-content:center;gap:12px;font-family:"Cinzel",serif;font-size:15px;color:var(--white);letter-spacing:1px}
.socials{left:670px;top:62px;display:flex;gap:18px;font-size:15px;font-weight:600;color:var(--white)}
.account{left:855px;top:30px;font-size:10px;letter-spacing:1.5px;color:var(--muted);word-spacing:10px}
.phone{left:855px;top:64px;font-size:10px;letter-spacing:1px;color:var(--muted);display:flex;align-items:center;gap:6px}
.cart{left:968px;top:60px;font-size:10px;letter-spacing:1px;color:var(--muted);display:flex;align-items:center;gap:8px}
.main-nav{left:0;top:108px;width:1200px;height:40px;background:var(--nav);border-top:1px solid #222;border-bottom:1px solid #222;display:flex;justify-content:center;align-items:center;gap:22px;font-family:"Cinzel",serif;font-size:11.5px;color:var(--white);letter-spacing:1px}
.main-nav .dot{width:4px;height:4px;border-radius:50%;background:var(--white)}

/* hero */
.hero{left:0;top:150px;width:1200px;height:680px;background:radial-gradient(ellipse at 70% 40%,#4a5865 0%,#26313b 40%,#141b22 75%,#0d1116 100%)}
.hero-photo{left:560px;top:0;width:640px;height:520px;background:radial-gradient(ellipse at 55% 45%,#c9a58f 0%,#8c6b5a 30%,#3f3a3c 60%,rgba(20,27,34,0) 80%)}
.hero-title{left:150px;top:80px;font-family:"Cinzel",serif;font-size:34px;font-weight:400;color:var(--green-bright);letter-spacing:2px}
.hero-sub{left:180px;top:125px;font-family:"Cinzel",serif;font-size:21px;color:var(--white);letter-spacing:1px}
.hero-rule{left:240px;top:162px;width:130px;height:1px;background:var(--line)}
.hero-script{left:90px;top:190px;width:460px;text-align:center;font-family:"Great Vibes",cursive;font-size:40px;line-height:46px;color:#d8d8d8}
.select{width:182px;height:32px;border:1px solid #888;background:rgba(10,14,18,.6);color:var(--white);font-size:9px;letter-spacing:.5px;display:flex;align-items:center;justify-content:space-between;padding:0 10px}
.go{left:418px;top:390px;font-family:"Cinzel",serif;font-size:30px;color:var(--white)}
.marketplace{left:118px;top:455px;font-size:13px;color:var(--white)}
.marketplace b{font-weight:600;margin-left:6px}
.slider-dots{left:582px;top:496px;display:flex;gap:8px}
.slider-dots span{width:6px;height:6px;border-radius:50%;background:#777}
.slider-dots span:first-child{background:var(--white)}
.category{top:528px;width:326px;height:142px;display:flex;flex-direction:column;align-items:flex-end;justify-content:center;padding-right:36px}
.category-label{font-family:"Cinzel",serif;font-size:16px;color:var(--white);margin-bottom:12px}
.btn{border:1px solid #bbb;color:var(--white);font-size:9px;letter-spacing:1px;padding:6px 14px;background:rgba(0,0,0,.3)}

/* sections */
.section-title{font-family:"Cinzel",serif;font-size:32px;font-weight:400;color:var(--green);letter-spacing:2px}
.section-intro{font-size:10.5px;color:var(--text);line-height:25px}
.welcome-title{left:0;top:870px;width:1200px;text-align:center}
.welcome-text{left:220px;top:922px;width:760px;text-align:center}
.welcome-rule{left:540px;top:1010px;width:120px;height:1px;background:var(--line)}
.arrows{display:flex;gap:6px}
.arrows span{width:20px;height:20px;border:1px solid #555;display:flex;align-items:center;justify-content:center}
.product-row{display:flex;gap:17px}
.product{width:186px}
.product-img{width:186px;height:186px}
.product-name{font-family:"Cinzel",serif;font-size:13px;font-weight:400;color:var(--white);text-align:center;margin-top:14px}
.product-meta{display:flex;justify-content:space-between;align-items:center;margin-top:12px;font-size:8.5px;line-height:17px;color:var(--muted)}
.product-meta .btn{font-size:8px;padding:6px 10px}

/* special */
.special{left:0;top:1905px;width:1200px;height:400px;background:radial-gradient(ellipse at 50% 50%,#1e1e1e,#0c0c0c 80%)}
.special-title{left:0;top:65px;width:1200px;text-align:center}
.special-item{top:150px;display:flex;gap:32px}
.special-img{width:224px;height:130px;background:#fff;display:flex;align-items:center;justify-content:center}
.special-name{font-family:"Cinzel",serif;font-size:19px;color:var(--white);font-weight:700;margin-top:-4px}
.special-desc{font-size:11px;color:#ddd;line-height:22px;margin-top:6px}
.special-meta{font-size:10px;color:var(--muted);margin-top:10px}

/* offer */
.offer-box{left:100px;top:2485px;width:1000px;height:240px;background:var(--panel)}
.offer-img{left:12px;top:12px;width:330px;height:216px;background:radial-gradient(ellipse at 50% 50%,#9a9a9a,#3a3a3a 55%,#151515)}
.offer-head{left:382px;top:28px;font-family:"Cinzel",serif;font-size:18px;color:var(--white)}
.offer-text{left:382px;top:62px;width:590px;font-size:11px;line-height:24px;color:var(--text)}

/* footer */
.site-footer{left:0;top:2760px;width:1200px;height:255px;background:#111;border-top:1px solid #222}
.footer-head{font-family:"Cinzel",serif;font-size:15px;color:var(--white);letter-spacing:1px}
.footer-links{font-size:8.5px;line-height:22px;color:var(--muted);letter-spacing:.5px;list-style:none}
.email{width:270px;height:28px;border:1px solid #666;font-size:8px;color:var(--muted);display:flex;align-items:center;padding-left:10px}
.badge{background:#555}
.bottom-bar{left:0;top:200px;width:1200px;height:55px;border-top:1px solid #2a2a2a;display:flex;align-items:center;padding:0 105px;font-size:8.5px;color:var(--muted);letter-spacing:.5px;gap:20px}
.social-dots{display:flex;gap:14px;margin-left:auto;align-items:center}
.social-dots i{width:10px;height:10px;border-radius:50%;background:#888;display:block}
</style>
</head>
<body>
<div class="page">

  <header class="site-header">
    <div class="abs brand"><span class="brand-mark"></span><span class="brand-name">KelvoraStonesUSA</span></div>
    <div class="abs brand-tag">Cut For Radiance</div>
    <div class="abs shipping">
      <svg width="36" height="20" viewBox="0 0 36 20"><rect x="0" y="2" width="22" height="12" fill="#2f9a4c"/><path d="M22 6h8l5 5v3H22z" fill="#2f9a4c"/><circle cx="7" cy="16" r="3" fill="#2f9a4c"/><circle cx="28" cy="16" r="3" fill="#2f9a4c"/></svg>
      FREE SHIPPING
    </div>
    <div class="abs socials"><span>Friendsy</span><span>Picturely</span></div>
    <div class="abs account">MY ACCOUNT &nbsp;/&nbsp; LOGIN &nbsp;/&nbsp; REGISTER</div>
    <div class="abs phone">
      <svg width="10" height="10" viewBox="0 0 10 10"><path d="M2 0l2 2-1 2 3 3 2-1 2 2-2 2C4 10 0 6 0 2z" fill="#8a8a8a"/></svg>
      (555) 014-0400
    </div>
    <div class="abs cart">
      <svg width="18" height="18" viewBox="0 0 18 18"><path d="M1 2h3l2 10h9l2-7H5" fill="none" stroke="#8a8a8a" stroke-width="1.4"/><circle cx="7" cy="15" r="1.5" fill="#8a8a8a"/><circle cx="14" cy="15" r="1.5" fill="#8a8a8a"/></svg>
      CART (0 : 0 ITEMS
    </div>
    <nav class="abs main-nav">
      <span>HOME</span><i class="dot"></i><span>GEMSTONES</span><i class="dot"></i><span>SHOWS</span><i class="dot"></i><span>SPECIAL GEMSTONES</span><i class="dot"></i><span>CARVINGS</span><i class="dot"></i><span>BEADS</span><i class="dot"></i><span>GOLD JEWELRY</span><i class="dot"></i><span>SILVER JEWELRY</span>
    </nav>
  </header>

  <section class="abs hero">
    <div class="abs hero-photo" role="img" aria-label="Portrait of a model wearing long diamond drop earrings"></div>
    <div class="abs hero-title">KELVORA STONES USA</div>
    <div class="abs hero-sub">CUT FOR RADIANCE</div>
    <div class="abs hero-rule"></div>
    <div class="abs hero-script">Kelvora Stones is a jewellery<br>online boutique</div>
    <div class="abs select" style="left:115px;top:308px">SHOP BY <span>&#9662;</span></div>
    <div class="abs select" style="left:310px;top:308px">SHOP BY STONE <span>&#9662;</span></div>
    <div class="abs select" style="left:115px;top:348px">SHOP BY SHAPE <span>&#9662;</span></div>
    <div class="abs select" style="left:310px;top:348px">SHOP BY COLORS <span>&#9662;</span></div>
    <div class="abs go">GO»</div>
    <div class="abs marketplace">Kelvora Stones on <b>Bidmarket</b></div>
    <div class="abs slider-dots"><span></span><span></span><span></span></div>

    <div class="abs category" style="left:120px;background:linear-gradient(90deg,#6e5a48,#b39a80 50%,#4a3a2e)" role="img" aria-label="Gold rings resting on a stone">
      <div class="category-label">GOLD JEWELRY</div><div class="btn">DISCOVER MORE</div>
    </div>
    <div class="abs category" style="left:455px;background:linear-gradient(90deg,#2a1e1c,#6a4a40 45%,#1a1414)" role="img" aria-label="Model wearing silver jewelry">
      <div class="category-label">SILVER JEWELRY</div><div class="btn">DISCOVER MORE</div>
    </div>
    <div class="abs category" style="left:790px;background:linear-gradient(90deg,#1a1a1a,#5a5a5a 40%,#222)" role="img" aria-label="Loose clear gemstones">
      <div class="category-label">SPECIAL GEMSTONES</div><div class="btn">DISCOVER MORE</div>
    </div>
  </section>

  <section>
    <h1 class="abs section-title welcome-title">WELCOME TO KELVORA STONES USA</h1>
    <p class="abs section-intro welcome-text">Kelvora Stones USA is an exciting new venture for the Kelvora Stones franchise. This dedicated sales office based in Harbor City is a great addition to our buying office in Velmora and manufacturing offices in Castelline and Orvanto.</p>
    <div class="abs welcome-rule"></div>
  </section>

  <section class="abs" style="left:100px;top:1048px;width:1000px">
    <h2 class="section-title">DIAMOND RINGS</h2>
    <div class="abs arrows" style="right:0;top:38px"><span><svg width="6" height="8"><path d="M5 0L1 4l4 4" stroke="#888" fill="none"/></svg></span><span><svg width="6" height="8"><path d="M1 0l4 4-4 4" stroke="#888" fill="none"/></svg></span></div>
    <p class="section-intro" style="margin-top:4px">Kelvora Stones USA is an exciting new venture for the Kelvora Stones franchise. This dedicated sales office based in Harbor City</p>
    <div class="product-row" style="margin-top:28px">
      <div class="product"><div class="product-img" style="background:radial-gradient(circle,#9a9a9a,#2a2a2a 70%)" role="img" aria-label="Platinum diamond band ring"></div><div class="product-name">AQUAMARINE RING</div><div class="product-meta"><span>7.05 CARATS<br>25.4 X 25.4 MM</span><span class="btn">VIEW DETAILS</span></div></div>
      <div class="product"><div class="product-img" style="background:radial-gradient(circle,#e8e8e8,#bdbdbd 60%,#f4f4f4)" role="img" aria-label="Diamond engagement ring set"></div><div class="product-name">AQUAMARINE RING</div><div class="product-meta"><span>7.05 CARATS<br>25.4 X 25.4 MM</span><span class="btn">VIEW DETAILS</span></div></div>
      <div class="product"><div class="product-img" style="background:radial-gradient(circle,#bdbdbd,#202020 70%)" role="img" aria-label="Loose diamonds on dark surface"></div><div class="product-name">AQUAMARINE RING</div><div class="product-meta"><span>7.05 CARATS<br>25.4 X 25.4 MM</span><span class="btn">VIEW DETAILS</span></div></div>
      <div class="product"><div class="product-img" style="background:radial-gradient(circle,#b58a6a,#3a2a20 50%,#050505)" role="img" aria-label="Gold ring with pink gemstone"></div><div class="product-name">AQUAMARINE RING</div><div class="product-meta"><span>7.05 CARATS<br>25.4 X 25.4 MM</span><span class="btn">VIEW DETAILS</span></div></div>
      <div class="product"><div class="product-img" style="background:radial-gradient(circle,#c9b0b0,#8a1818 55%,#4a0808)" role="img" aria-label="Diamond rings on red background"></div><div class="product-name">AQUAMARINE RING</div><div class="product-meta"><span>7.05 CARATS<br>25.4 X 25.4 MM</span><span class="btn">VIEW DETAILS</span></div></div>
    </div>
  </section>

  <section class="abs" style="left:100px;top:1458px;width:1000px">
    <h2 class="section-title">NEW ARRIVALS</h2>
    <div class="abs arrows" style="right:0;top:38px"><span><svg width="6" height="8"><path d="M5 0L1 4l4 4" stroke="#888" fill="none"/></svg></span><span><svg width="6" height="8"><path d="M1 0l4 4-4 4" stroke="#888" fill="none"/></svg></span></div>
    <p class="section-intro" style="margin-top:4px">Kelvora Stones USA is an exciting new venture for the Kelvora Stones franchise. This dedicated sales office based in Harbor City</p>
    <div class="product-row" style="margin-top:28px">
      <div class="product"><div class="product-img" style="background:radial-gradient(circle,#7a7a7a,#0a0a0a 65%)" role="img" aria-label="Clear gemstones on black"></div><div class="product-name">AQUAMARINE RING</div><div class="product-meta"><span>7.05 CARATS<br>25.4 X 25.4 MM</span><span class="btn">VIEW DETAILS</span></div></div>
      <div class="product"><div class="product-img" style="background:radial-gradient(circle,#3a6ac0,#0c2a6a 50%,#f2f2f2 75%)" role="img" aria-label="Blue sapphire gemstone"></div><div class="product-name">AQUAMARINE RING</div><div class="product-meta"><span>7.05 CARATS<br>25.4 X 25.4 MM</span><span class="btn">VIEW DETAILS</span></div></div>
      <div class="product"><div class="product-img" style="background:radial-gradient(circle,#e0e0e0,#6a6a6a 45%,#050505 75%)" role="img" aria-label="Brilliant cut diamond"></div><div class="product-name">AQUAMARINE RING</div><div class="product-meta"><span>7.05 CARATS<br>25.4 X 25.4 MM</span><span class="btn">VIEW DETAILS</span></div></div>
      <div class="product"><div class="product-img" style="background:radial-gradient(circle,#d08a50,#6a4010 45%,#050505 75%)" role="img" aria-label="Gold ring with amber gemstone"></div><div class="product-name">AQUAMARINE RING</div><div class="product-meta"><span>7.05 CARATS<br>25.4 X 25.4 MM</span><span class="btn">VIEW DETAILS</span></div></div>
      <div class="product"><div class="product-img" style="background:radial-gradient(circle,#d4d4d4,#fafafa 60%)" role="img" aria-label="Scattered diamonds on white"></div><div class="product-name">AQUAMARINE RING</div><div class="product-meta"><span>7.05 CARATS<br>25.4 X 25.4 MM</span><span class="btn">VIEW DETAILS</span></div></div>
    </div>
  </section>

  <section class="abs special">
    <h2 class="abs section-title special-title">SPECIAL PRODUCTS</h2>
    <div class="abs arrows" style="right:100px;top:75px"><span><svg width="6" height="8"><path d="M5 0L1 4l4 4" stroke="#888" fill="none"/></svg></span><span><svg width="6" height="8"><path d="M1 0l4 4-4 4" stroke="#888" fill="none"/></svg></span></div>
    <div class="abs special-item" style="left:100px">
      <div class="special-img"><div style="width:180px;height:104px;background:linear-gradient(135deg,#9ad0cc,#3f8a88 50%,#b8e4e0)" role="img" aria-label="Octagon cut aquamarine gemstone"></div></div>
      <div><div class="special-name">AQUAMARINE RING</div><div class="special-desc">1.24 Carats Natural Aquamarine<br>Loose Gemstone - Octagon</div><div class="special-meta">7.05 CARATS, 25.4 X 25.4 MM</div><div class="btn" style="display:inline-block;margin-top:18px;font-size:8px">VIEW DETAILS</div></div>
    </div>
    <div class="abs special-item" style="left:628px">
      <div class="special-img"><div style="width:140px;height:110px;border-radius:50%;background:radial-gradient(circle,#c4ecea,#5aa6a6 60%,#2a6a6e)" role="img" aria-label="Oval cut aquamarine gemstone"></div></div>
      <div><div class="special-name">AQUAMARINE RING</div><div class="special-desc">1.24 Carats Natural Aquamarine<br>Loose Gemstone - Octagon</div><div class="special-meta">7.05 CARATS, 25.4 X 25.4 MM</div><div class="btn" style="display:inline-block;margin-top:18px;font-size:8px">VIEW DETAILS</div></div>
    </div>
  </section>

  <section class="abs" style="left:100px;top:2345px;width:1000px">
    <h2 class="section-title">OFFER OF THE MONTH</h2>
    <div class="abs arrows" style="right:0;top:80px"><span><svg width="6" height="8"><path d="M5 0L1 4l4 4" stroke="#888" fill="none"/></svg></span><span><svg width="6" height="8"><path d="M1 0l4 4-4 4" stroke="#888" fill="none"/></svg></span></div>
    <p class="section-intro" style="margin-top:10px;width:760px">Kelvora Stones USA is an exciting new venture for the Kelvora Stones franchise. This dedicated sales office based in Harbor City is a great addition to our buying office in Velmora and manufacturing offices in Castelline and Orvanto.</p>
  </section>
  <div class="abs offer-box">
    <div class="abs offer-img" role="img" aria-label="Diamond halo ring with split pavé band"></div>
    <div class="abs offer-head">LOREM IPSUM IS SIMPLY DUMMY TEXT OF THE PRINTING</div>
    <p class="abs offer-text">Lorem Ipsum is simply dummy text of the printing and typesetting industry. Lorem Ipsum has been the industry's standard dummy text ever since the 1500s, when an unknown printer took a galley of type and scrambled it to make a type specimen book. It has survived not only five centuries, but also the leap into electronic typesetting, remaining essentially unchanged.</p>
    <div class="abs btn" style="left:382px;top:185px;font-size:8.5px">VIEW MORE DETAILS</div>
  </div>

  <footer class="abs site-footer">
    <div class="abs footer-head" style="left:105px;top:22px">KELVORA STONES USA</div>
    <ul class="abs footer-links" style="left:105px;top:56px"><li>WHO WE ARE</li><li>OUR HISTORY</li><li>THE CONCEPT</li><li>PRODUCT SHOWCASE</li><li>A QUICK DEDICATION IN JEWELLERY</li></ul>
    <ul class="abs footer-links" style="left:302px;top:56px"><li>OUR PROCESS</li><li>WHERE WE OPERATE</li><li>OUR PROMISE</li><li>A QUOTATION FORM</li><li>OUR CONTACT</li></ul>
    <ul class="abs footer-links" style="left:458px;top:56px"><li>OUR LOCATION</li><li>FAQS</li><li>DISCLAIMERS AND LEGAL INFO</li><li>NEWS</li><li>BLOG</li></ul>
    <div class="abs footer-head" style="left:638px;top:22px">NEWSLETTER SIGNUP</div>
    <div class="abs footer-links" style="left:638px;top:50px">GET OUR RECENT UPDATES THROUGH YOUR EMAIL ID</div>
    <div class="abs email" style="left:638px;top:84px">ENTER YOUR EMAIL ID</div>
    <div class="abs btn" style="left:638px;top:126px;font-size:8px">SUBSCRIBE</div>
    <div class="abs badge" style="left:978px;top:24px;width:84px;height:32px"></div>
    <div class="abs badge" style="left:962px;top:66px;width:26px;height:26px;border-radius:50%"></div>
    <div class="abs badge" style="left:994px;top:70px;width:70px;height:20px"></div>
    <div class="abs badge" style="left:980px;top:108px;width:82px;height:58px"></div>
    <div class="abs bottom-bar">
      <span>© 2016 : KELVORA STONES USA ALL RIGHTS RESERVED</span><span>/</span><span>TERMS &amp; CONDITIONS</span><span>/</span><span>PRIVACY POLICY</span><span>/</span><span>DISCLAIMER</span>
      <div class="social-dots"><span>CONNECT WITH OUR SOCIAL NETWORK</span><i></i><i></i><i></i><i></i><i></i></div>
    </div>
  </footer>

</div>
</body>
</html>
```